Web Design Project

Looking for an eye catching banner page to be used on the website and LinkedIn. We are an Executive Recruiting and HR Consulting service firm with a modern edge. We want to demonstrate through our brand that we are using the latest recruiting trends to find talent and that we are easy to work with- innovative and simple.We typically recruit for Engineers, IT professionals, Accounting and Operation Managers. Our website is www.bluvantatalent.com and it needs a fresh clean look. We love our logo but might want to use the "8" to show the 2 sides of our business or maybe to use the infinity concept or continuous improvement. We like the Green and white colors with accents in gray.

Target Market(s)

Small to mid-sized Business Managers seeking innovation

Industry/Entity Type

Business

Requirements
Must have
• Use of the 8
Long picture on top to be used on LinkedIn and the website top
Clean Simple look- modern font like century gothic
Nice to have
• Smiling face(s)
Layered image of 8 or of photo stock faces
Maybe a modern office so they feel that they walked in to meet us (fyi our office has white chandeliers and green walls that match our logo)
Should not have
• Busy or cluttered feel

```html
<!DOCTYPE html>
<html lang="en">
<head>
<meta charset="utf-8">
<title>Bluvanta — Recruiting and HR Consulting</title>
<link rel="stylesheet" href="https://fonts.googleapis.com/css2?family=Questrial&family=Arimo:wght@400;700&display=swap">
<style>
:root{
  --green:#8cb52c;
  --green-light:#a9cb4e;
  --green-pale:#e9f2d3;
  --green-dark:#6c9424;
  --footer-green:#769f2f;
  --gray-dark:#55595f;
  --gray:#7d8288;
  --gray-light:#a5a9ad;
  --gray-pale:#eceeed;
  --text:#3c3f42;
  --white:#ffffff;
}
*{box-sizing:border-box;margin:0;padding:0}
html,body{width:1000px;height:1200px;overflow:hidden;background:var(--white)}
body{position:relative;font-family:"Arimo",Arial,sans-serif;color:var(--text);font-size:9px}
.abs{position:absolute}
.top-strip{left:0;top:0;width:1000px;height:6px;background:var(--green-light)}
.top-notch{left:318px;top:6px;width:0;height:0;border-left:7px solid transparent;border-right:7px solid transparent;border-top:7px solid var(--green-light)}

/* header */
.brand-name{left:187px;top:52px;font-family:"Arimo",Arial,sans-serif;font-weight:700;font-size:30px;color:var(--gray-dark);letter-spacing:.5px;line-height:1}
.util-links{right:188px;top:22px;display:flex;gap:12px;font-size:9px;font-weight:700;color:var(--text)}
.util-links span{display:flex;align-items:center;gap:3px}
.btn-role{top:56px;width:93px;height:26px;border-radius:3px;color:var(--white);font-family:"Questrial",sans-serif;font-size:13px;display:flex;align-items:center;justify-content:center}
.btn-candidate{left:619px;background:linear-gradient(#b7d566,#93bb3a);border:1px solid #86ad30}
.btn-clients{left:719px;background:linear-gradient(#8a8f95,#5e6369);border:1px solid #55595f}
.search{left:686px;top:92px;width:126px;height:20px;border:1px solid #cfd2d4;border-radius:2px;font-size:9px;font-style:italic;color:#9a9ea2;padding:4px 7px}
.search svg{position:absolute;right:6px;top:4px}

.main-nav{left:186px;top:120px;width:626px;height:31px;background:linear-gradient(#9cc245,#86ad2f);border:1px solid #7ca12b;display:flex;align-items:center;padding-left:44px;gap:15px;font-size:9px;color:var(--white);white-space:nowrap}
.main-nav .active{border-bottom:2px solid #c7df8f;padding-bottom:2px}

/* hero */
.hero{left:0;top:160px;width:1000px;height:217px;background:linear-gradient(90deg,#e7eed4 0%,#f6f7ee 25%,#c9da8f 45%,#dfe9b7 70%,#bccf76 100%)}
.hero-caption{left:186px;top:338px;width:626px;height:39px;background:rgba(110,115,120,.72);color:var(--white);font-size:12.5px;text-align:center;line-height:15px;padding-top:4px}

/* intro */
.intro-line{left:186px;top:416px;width:626px;height:1px;background:var(--green-light)}
.intro-title{right:188px;top:386px;font-family:"Questrial",sans-serif;font-weight:400;font-size:21px;color:var(--gray-dark)}
.intro-copy{left:186px;top:454px;width:620px;font-size:8.6px;line-height:11.5px}
.intro-copy p{margin-bottom:8px}
.btn-small{height:16px;border-radius:2px;background:linear-gradient(#b3d262,#8db635);color:var(--white);font-size:8px;font-weight:700;display:flex;align-items:center;justify-content:center}
.learn-more{left:745px;top:514px;width:58px}

/* services */
.services{left:0;top:544px;width:1000px;height:120px;background:#f4f5f4;border-top:1px solid #e1e3e2;border-bottom:1px solid #e1e3e2}
.service{top:552px;width:180px;text-align:center;font-size:11px;color:var(--text)}
.service-icon{width:74px;height:74px;border-radius:50%;margin:0 auto 16px;background:radial-gradient(circle at 50% 35%,#9a9fa4,#6d7277);box-shadow:0 5px 6px rgba(0,0,0,.18);display:flex;align-items:center;justify-content:center}
.service-icon.is-active{background:radial-gradient(circle at 50% 35%,#b5dc4f,#74a91d)}

/* numbers */
.numbers{left:186px;top:684px;width:414px;height:199px;background:#f0f1ec;border:1px solid #d9dcd3}
.numbers-head{height:31px;background:linear-gradient(#a8cd47,#86b02a);display:flex;align-items:center;padding-left:14px;color:var(--white);font-family:"Questrial",sans-serif;font-size:16px}
.numbers ul{list-style:none;padding:10px 22px 0 10px;font-size:8.5px;line-height:12.5px}
.numbers li{display:flex;gap:7px;padding:4px 0 8px;border-bottom:1px dotted #c9ccc2;margin-bottom:4px}
.numbers li:last-child{border-bottom:none}
.numbers li svg{flex:none;margin-top:1px}
.scroll-track{left:588px;top:724px;width:6px;height:150px;border:1px solid #c8cbc4;border-radius:3px;background:var(--white)}
.scroll-thumb{left:589px;top:725px;width:4px;height:36px;border-radius:2px;background:#b7bab3}

/* testimonials */
.testimonials{left:619px;top:684px;width:193px;height:199px;background:var(--white);border:1px solid #dedfdc}
.testimonials h3{position:absolute;left:16px;top:10px;font-family:"Questrial",sans-serif;font-weight:400;font-size:17px;color:var(--text)}
.testimonials p{position:absolute;left:16px;top:50px;width:160px;font-size:8.4px;line-height:12px;text-align:justify}
.testimonials .who{position:absolute;right:22px;top:140px;font-size:8.4px;font-weight:700;font-style:italic}
.more-testimonials{left:719px;top:859px;width:86px}

/* news */
.news{left:186px;top:902px;width:626px;height:36px;background:linear-gradient(#b3b6b9,#9a9ea2);display:flex;align-items:center;color:var(--white)}
.news-label{width:132px;height:100%;background:linear-gradient(#6d7176,#54585d);display:flex;align-items:center;gap:10px;padding-left:10px;font-family:"Questrial",sans-serif;font-size:14px;clip-path:polygon(0 0,92% 0,100% 50%,92% 100%,0 100%)}
.news-text{flex:1;padding-left:8px;font-size:10px}
.news-arrow{width:30px;text-align:center}

/* footer */
.footer{left:0;top:960px;width:1000px;height:210px;background:linear-gradient(#7da734,#6d972a)}
.foot-col{top:972px;color:var(--white);font-size:8.6px}
.foot-col h4{font-family:"Questrial",sans-serif;font-weight:400;font-size:13px;padding-bottom:6px;border-bottom:1px solid rgba(255,255,255,.45);margin-bottom:8px;width:100px}
.foot-col li{list-style:none;margin-bottom:6px}
.contact-row{display:flex;align-items:center;gap:8px;margin-bottom:10px}
.phone{font-size:13px}
.cert-badge{left:189px;top:1106px;width:104px;height:48px;border-radius:6px;background:var(--white);border:2px solid #dfe8cc}
.jobs{left:469px;top:976px;width:157px;height:178px;background:var(--white);border:1px solid #d8dccf}
.jobs-head{height:24px;background:linear-gradient(#a9cd48,#88b12c);color:var(--white);font-family:"Questrial",sans-serif;font-size:13px;text-align:center;line-height:24px}
.jobs ul{list-style:none;padding:8px 10px;font-size:8.4px;line-height:11px;color:var(--text)}
.jobs li{margin-bottom:7px}
.more-vacancies{left:507px;top:1129px;width:84px}
.social-box{left:643px;top:976px;width:160px;height:178px;background:var(--white);border:1px solid #d8dccf;font-size:8px;color:var(--text)}
.social-box .sb-title{position:absolute;left:10px;top:10px;font-size:11px;font-weight:700;color:var(--gray-dark)}
.social-box .sb-like{position:absolute;left:68px;top:9px;width:28px;height:14px;border:1px solid #c5c9cf;border-radius:2px;background:#f2f3f5;font-size:7.5px;text-align:center;line-height:12px}
.social-box .sb-count{position:absolute;left:4px;top:42px;font-size:7px}
.social-box .sb-grid{position:absolute;left:8px;top:60px;width:142px;height:76px;background:linear-gradient(135deg,#c9ccd0,#9fa4aa)}
.social-box .sb-foot{position:absolute;left:0;bottom:0;width:100%;height:18px;border-top:1px solid #e1e3e6;font-size:7px;padding:5px 6px;color:#6b6f75}
.bottom-bar{left:0;top:1170px;width:1000px;height:30px;background:linear-gradient(#5d6166,#45494e);color:#e6e7e8;font-size:8.4px;text-align:center;line-height:30px}

/* share rail */
.share-rail{left:974px;top:388px;width:22px;display:flex;flex-direction:column;gap:3px}
.share-rail span{display:block;width:22px;height:22px;border-radius:2px}
</style>
</head>
<body>
<div class="abs top-strip"></div>
<div class="abs top-notch"></div>

<header>
  <div class="abs brand-name">BLUVANTA</div>
  <div class="abs util-links">
    <span><svg width="10" height="9" viewBox="0 0 10 9"><path d="M5 0 0 4h1.5v5h2.5V6h2v3h2.5V4H10z" fill="#3c3f42"/></svg>Home</span>
    <span><svg width="11" height="8" viewBox="0 0 11 8"><rect x=".5" y=".5" width="10" height="7" fill="none" stroke="#3c3f42"/><path d="M.5.5 5.5 4l5-3.5" fill="none" stroke="#3c3f42"/></svg>Contact</span>
  </div>
  <div class="abs btn-role btn-candidate">Candidate</div>
  <div class="abs btn-role btn-clients">Clients</div>
  <div class="abs search">Search<svg width="11" height="11" viewBox="0 0 11 11"><circle cx="4.5" cy="4.5" r="3.5" fill="none" stroke="#9a9ea2" stroke-width="1.4"/><path d="M7 7l3.5 3.5" stroke="#9a9ea2" stroke-width="1.6"/></svg></div>
  <nav class="abs main-nav">
    <span class="active">Recruiting Services</span><span>HR consulting Services</span><span>Testimonials</span><span>Job Openings</span><span>Job Search Assistance</span><span>Job Application</span><span>Blog</span>
  </nav>
</header>

<section>
  <div class="abs hero" role="img" aria-label="Photo of five smiling recruiting professionals in a bright green-walled modern office lounge with orange chairs"></div>
  <div class="abs hero-caption">Bluvanta demonstrated extraordinary insight in understanding both the client recruiting<br>needs and the candidates' objectives"</div>
</section>

<section>
  <div class="abs intro-line"></div>
  <h2 class="abs intro-title">Where strategy meets recruiting</h2>
  <div class="abs intro-copy">
    <p>The modern and successful recruiting leader begins with a strategic foundation, leverages connectivity through social media, stakeholder relationships and builds pipelines of competencies, quickly and flexibly to solve pressing employment challenges.</p>
    <p>Bluvanta combines strategy and action to find top talent in the areas of Engineering, IT, Operations, and Accounting and Administration. Look to Bluvanta to explore new pathways to strategic relevancy.&nbsp; From strategy to execution, we are the team you need… NOW!</p>
    <p>How can we be your strategic partner to success?</p>
  </div>
  <div class="abs btn-small learn-more">Learn more</div>
</section>

<section>
  <div class="abs services"></div>
  <div class="abs service" style="left:196px">
    <div class="service-icon"><svg width="40" height="28" viewBox="0 0 40 28"><circle cx="13" cy="8" r="6" fill="#3f4347"/><path d="M2 27c0-8 5-12 11-12s11 4 11 12z" fill="#3f4347"/><circle cx="27" cy="8" r="6" fill="#4a4e52"/><path d="M16 27c0-8 5-12 11-12s11 4 11 12z" fill="#4a4e52"/></svg></div>
    Expert Recruiting
  </div>
  <div class="abs service" style="left:408px">
    <div class="service-icon"><svg width="40" height="22" viewBox="0 0 40 22"><rect x="2" y="4" width="16" height="14" fill="#ffffff"/><circle cx="18" cy="11" r="3" fill="#ffffff"/><rect x="22" y="4" width="16" height="14" fill="#3f4347"/></svg></div>
    Recruiting Strategy
  </div>
  <div class="abs service" style="left:623px">
    <div class="service-icon is-active"><svg width="34" height="34" viewBox="0 0 34 34"><circle cx="17" cy="10" r="7" fill="#2f3336"/><path d="M3 34c0-10 6-15 14-15s14 5 14 15z" fill="#2f3336"/><path d="M15 19h4l-2 3z" fill="#ffffff"/></svg></div>
    Human Resource Consulting
  </div>
</section>

<section class="abs numbers">
  <div class="numbers-head">Here at Bluvanta, we love our numbers!</div>
  <ul>
    <li><svg width="10" height="10" viewBox="0 0 10 10"><circle cx="5" cy="5" r="5" fill="#8cb52c"/><path d="M4 2.5 6.5 5 4 7.5" fill="none" stroke="#fff" stroke-width="1.4"/></svg>8 is known as the beginning and long symbolized for good luck, to us it means that and more!</li>
    <li><svg width="10" height="10" viewBox="0 0 10 10"><circle cx="5" cy="5" r="5" fill="#8cb52c"/><path d="M4 2.5 6.5 5 4 7.5" fill="none" stroke="#fff" stroke-width="1.4"/></svg>76% of all employees are passively searching for a new position, we must find ways to keep your talent engaged as well as identiy the right new talent for your organization</li>
    <li><svg width="10" height="10" viewBox="0 0 10 10"><circle cx="5" cy="5" r="5" fill="#8cb52c"/><path d="M4 2.5 6.5 5 4 7.5" fill="none" stroke="#fff" stroke-width="1.4"/></svg>52% of companies are expecting to grow in the next 6 months</li>
    <li><svg width="10" height="10" viewBox="0 0 10 10"><circle cx="5" cy="5" r="5" fill="#8cb52c"/><path d="M4 2.5 6.5 5 4 7.5" fill="none" stroke="#fff" stroke-width="1.4"/></svg>$8,947 is the national average cost per hire—up approximately 57% from $5,708 in 2009, we can show you how to reduce the cost and increase quality</li>
  </ul>
</section>
<div class="abs scroll-track"></div>
<div class="abs scroll-thumb"></div>

<section class="abs testimonials">
  <h3>Testimonials</h3>
  <p>Bluvanta has been very attentive to the needs of our Corporation. From providing administrative to technical candidates, they operate in a professional manor and will go above and beyond to achieve exceptional results.</p>
  <span class="who">Federal Contract Company</span>
</section>
<div class="abs btn-small more-testimonials">More Testimonials</div>

<div class="abs news">
  <div class="news-label"><svg width="16" height="12" viewBox="0 0 16 12"><rect x="1" y="1" width="14" height="10" rx="2" fill="none" stroke="#fff" stroke-width="1.5"/><circle cx="10" cy="6" r="2" fill="#fff"/></svg>What's new!</div>
  <div class="news-text">Bluvanta received best organization award of the year!! yeah we're excited!!!</div>
  <div class="news-arrow"><svg width="8" height="12" viewBox="0 0 8 12"><path d="M1.5 1.5 6 6l-4.5 4.5" fill="none" stroke="#fff" stroke-width="2"/></svg></div>
</div>

<footer>
  <div class="abs footer"></div>
  <div class="abs foot-col" style="left:191px">
    <h4>About Bluvanta</h4>
    <ul><li>About Us</li><li>What we do</li><li>How we do</li><li>Testimonials</li><li>Our awards</li><li>Our Partners</li></ul>
  </div>
  <div class="abs cert-badge"></div>
  <div class="abs foot-col" style="left:317px">
    <h4>Contact Us</h4>
    <ul><li>Contact Bluvanta</li><li>Help &amp; Links</li></ul>
    <div class="contact-row" style="margin-top:10px"><svg width="10" height="14" viewBox="0 0 10 14"><path d="M5 0a5 5 0 0 0-5 5c0 4 5 9 5 9s5-5 5-9a5 5 0 0 0-5-5z" fill="#fff"/><circle cx="5" cy="5" r="2" fill="#769f2f"/></svg><span>2210 Harbor Crest Blvd<br>Houston, TX, 77062</span></div>
    <div class="contact-row"><svg width="14" height="10" viewBox="0 0 14 10"><rect x=".5" y=".5" width="13" height="9" fill="none" stroke="#fff"/><path d="M.5.5 7 5.5l6.5-5" fill="none" stroke="#fff"/></svg><span>info@bluvantatalent.com</span></div>
    <div class="contact-row phone"><svg width="13" height="13" viewBox="0 0 13 13"><path d="M3 0 5 3 3.5 4.5c1 2 3 4 5 5L10 8l3 2-1.5 2.5C6 12 1 7 .5 1.5z" fill="#fff"/></svg><span>281.555.0142</span></div>
    <div class="contact-row phone"><svg width="14" height="12" viewBox="0 0 14 12"><rect x="3" y="0" width="8" height="4" fill="#fff"/><rect x="0" y="4" width="14" height="5" fill="#fff"/><rect x="3" y="8" width="8" height="4" fill="#fff" stroke="#769f2f"/></svg><span>713.555.0198</span></div>
  </div>
  <div class="abs jobs">
    <div class="jobs-head">Job Openings</div>
    <ul>
      <li>- Houstan is hiring</li>
      <li>- Northwind Consulting is looking for a decent Art director</li>
      <li>- Corelink Systems is hiring developer</li>
      <li>- Northwind Consulting is looking for a decent designer</li>
    </ul>
  </div>
  <div class="abs btn-small more-vacancies">More Vacancies</div>
  <div class="abs social-box">
    <span class="sb-title">Bluvanta</span>
    <span class="sb-like">Like</span>
    <span class="sb-count">8,046 people like Bluvanta</span>
    <div class="sb-grid" role="img" aria-label="Grid of follower profile photos"></div>
    <div class="sb-foot">Social feed plugin</div>
  </div>
  <div class="abs bottom-bar">Copyright © 2013 Bluvanta All rights reserved.&nbsp; /&nbsp;&nbsp; Site Map&nbsp; /&nbsp;&nbsp; Disclaimers</div>
</footer>

<div class="abs share-rail" aria-label="Share links">
  <span style="background:#4a6aa8"></span>
  <span style="background:#6b7075"></span>
  <span style="background:#2f7fb0"></span>
  <span style="background:#d9dcdf"></span>
  <span style="background:#49a9d8"></span>
  <span style="background:#e48a2a"></span>
</div>
</body>
</html>
```